Pyschiatry Experts need Marketing Campaign

Ad(s) developed for print advertising sharing our purpose and services, highlighting our medical care providers. Must be welcoming and inviting while displaying a high level of professionalism expected from a physician's office.

Target Market(s)

Local community

Industry/Entity Type

Psychiatry (Healthcare)

Requirements
Must have
• Staff pictures, 'Medication Management Experts', 'Prompt Appointments', 'ADD/ADHD, Bipolar Disorder, Depression, Anxiety, Schizophrenia, Grief Reaction and others' 'Virtual and In-Person Visits'
Nice to have
• Address: 412 E Marlowe Coeur d'Alene Phone (208)555-7193 website: BrightLoftCare.com Hours: Mon - Thur 7am - 6pm

```html
<!DOCTYPE html>
<html lang="en">
<head>
<meta charset="utf-8">
<title>BrightLoft Care – Mental Health Evaluations</title>
<link rel="stylesheet" href="https://fonts.googleapis.com/css2?family=Playfair+Display:wght@700;800&family=Poppins:wght@400;500;600&display=swap">
<style>
  :root{
    --teal:#138d80;
    --teal-dark:#0c6f63;
    --lime:#8fd14f;
    --cream:#f1ebdc;
    --sage:#e3e8c8;
    --ink:#1f1f1f;
    --paper:#ffffff;
    --wash:#fbf6d6;
  }
  *{box-sizing:border-box;margin:0;padding:0}
  html,body{width:949px;height:1200px;overflow:hidden;background:var(--paper)}
  .flyer{
    position:relative;width:949px;height:1200px;overflow:hidden;
    background:
      radial-gradient(ellipse 420px 300px at 200px 160px,var(--wash),transparent 75%),
      radial-gradient(ellipse 360px 120px at 700px 30px,#fcf7dc,transparent 80%),
      var(--paper);
    font-family:"Poppins",sans-serif;color:var(--ink);
  }
  .serif{font-family:"Playfair Display",serif}

  .hero-photo{
    position:absolute;left:40px;top:22px;width:400px;height:395px;border-radius:200px 200px 24px 24px;
    background:radial-gradient(circle at 50% 40%,#c9e99a 0%,#a8dc63 45%,#eef6d4 80%,transparent 100%);
  }
  .badge-main{
    position:absolute;left:48px;top:412px;width:376px;height:69px;
    background:var(--teal);border-radius:28px 40px 0 28px;
    color:#fff;font-size:24px;font-weight:700;line-height:30px;padding:12px 0 0 14px;
    box-shadow:0 10px 14px -8px rgba(0,0,0,.25);white-space:nowrap;
  }
  .badge-tag{
    position:absolute;left:267px;top:466px;width:137px;height:42px;
    background:var(--lime);color:#1c1c1c;font-size:25px;font-weight:700;
    text-align:center;line-height:42px;border-radius:6px 6px 0 0;
  }

  .headline{position:absolute;left:468px;top:38px}
  .headline .lead{font-size:37px;font-weight:700;color:#2a2a2a;line-height:1.15}
  .headline .main{font-size:58px;font-weight:700;color:var(--teal);line-height:1;margin-top:2px}
  .intro{
    position:absolute;left:472px;top:240px;border-left:3px solid var(--teal);
    padding-left:16px;font-size:19px;line-height:28px;color:#222;
  }
  .perk{
    position:absolute;left:463px;width:435px;height:70px;border-radius:35px;
    background:var(--cream);display:flex;align-items:center;padding-left:18px;gap:18px;
    font-size:22px;font-weight:700;white-space:nowrap;
  }
  .perk svg{width:36px;height:36px;flex:none}

  .expertise-title{position:absolute;left:53px;top:563px;font-size:38px;font-weight:700;line-height:40px}
  .expertise-title .accent{color:var(--teal)}
  .condition{position:absolute;display:flex;align-items:center;gap:12px;font-size:15px;font-weight:600;line-height:20px;white-space:nowrap}
  .condition .icon{width:60px;height:60px;border-radius:50%;background:var(--lime);border:2px solid #fff;box-shadow:0 0 0 1.5px var(--teal);flex:none}
  .condition .light{font-weight:400}
  .divider{position:absolute;top:570px;height:128px;border-left:1.5px dashed #777}

  .providers{position:absolute;left:52px;top:735px;width:845px;height:238px}
  .providers-head{
    height:46px;background:var(--teal);border-radius:32px 60px 0 0;color:#fff;
    display:flex;align-items:center;justify-content:center;
    font-size:21px;font-weight:700;letter-spacing:1.5px;line-height:1.2;white-space:nowrap;
  }
  .provider-row{display:flex;height:192px;border-radius:0 0 0 28px;overflow:hidden;box-shadow:0 12px 16px -12px rgba(0,0,0,.25)}
  .provider{flex:1;text-align:center;padding-top:18px}
  .provider:nth-child(odd){background:var(--cream)}
  .provider:nth-child(even){background:var(--sage)}
  .provider .portrait{width:110px;height:110px;border-radius:50%;margin:0 auto;background:radial-gradient(circle at 50% 45%,#9aa3a8,#4e5960)}
  .provider .name{font-weight:600;font-size:15px;line-height:20px;margin-top:12px}
  .provider .cred{font-size:11.5px;line-height:14px}

  .brand{position:absolute;left:40px;top:1075px;width:330px;display:flex;align-items:center;justify-content:center;gap:12px}
  .brand .dot{width:26px;height:26px;border-radius:50%;background:var(--lime);flex:none}
  .brand .name{font-size:28px;font-weight:700;color:var(--teal);letter-spacing:.5px;white-space:nowrap;line-height:1.2}

  .contact{position:absolute;left:419px;top:1018px;font-size:17px;color:#222}
  .contact li{list-style:none;display:flex;align-items:center;gap:12px;height:36px;white-space:nowrap}
  .contact svg{width:18px;height:18px;flex:none}

  .hours{position:absolute;left:411px;top:1131px;width:485px;height:44px;display:flex;border-radius:8px;overflow:hidden;color:#fff;font-size:20px;font-weight:600}
  .hours span{display:flex;align-items:center;justify-content:center}
  .hours .label{width:130px;background:var(--lime);font-size:18px}
  .hours .days{width:180px;background:var(--teal-dark)}
  .hours .time{flex:1;background:var(--teal)}
</style>
</head>
<body>
<main class="flyer">
  <div class="hero-photo" role="img" aria-label="Woman meditating cross-legged in front of large green leaves"></div>
  <div class="badge-main serif">Medication Management</div>
  <div class="badge-tag serif">Experts</div>

  <header class="headline serif">
    <div class="lead">Comprehensive</div>
    <h1 class="main">Mental Health<br>Evalutions</h1>
  </header>
  <p class="intro">Mental Health and Psychiatry<br>Services Migraine and<br>Neurospasticity Intervention</p>

  <div class="perk serif" style="top:352px">
    <svg viewBox="0 0 36 36"><circle cx="18" cy="18" r="16" fill="var(--teal)"/><path d="M11 18.5l5 5 9-10" fill="none" stroke="#fff" stroke-width="3.2" stroke-linecap="round" stroke-linejoin="round"/></svg>
    Prompt Appointments
  </div>
  <div class="perk serif" style="top:434px">
    <svg viewBox="0 0 36 36"><circle cx="18" cy="18" r="16" fill="var(--teal)"/><path d="M11 18.5l5 5 9-10" fill="none" stroke="#fff" stroke-width="3.2" stroke-linecap="round" stroke-linejoin="round"/></svg>
    Virtual and In-Person Visits
  </div>

  <h2 class="expertise-title serif">We<br><span class="accent">expertise<br>in</span></h2>

  <div class="condition" style="left:270px;top:570px"><span class="icon" role="img" aria-label="ADHD head icon"></span>ADD/ADHD</div>
  <div class="condition" style="left:270px;top:636px"><span class="icon" role="img" aria-label="Bipolar disorder head icon"></span>Bipolar<br>Disorder</div>
  <div class="divider" style="left:465px"></div>
  <div class="condition" style="left:488px;top:566px"><span class="icon" role="img" aria-label="Depression icon"></span>Depression</div>
  <div class="condition" style="left:488px;top:636px"><span class="icon" role="img" aria-label="Anxiety icon"></span>Anxiety</div>
  <div class="divider" style="left:662px"></div>
  <div class="condition" style="left:702px;top:562px"><span class="icon" role="img" aria-label="Schizophrenia head icon"></span>Schizophrenia</div>
  <div class="condition" style="left:702px;top:636px"><span class="icon" role="img" aria-label="Grief reaction head icon"></span><span>Grief Reaction<br><span class="light">and others</span></span></div>

  <section class="providers">
    <h2 class="providers-head serif">MEET OUR MENTAL&nbsp; HEALTH PROVIDERS</h2>
    <div class="provider-row">
      <div class="provider"><div class="portrait" role="img" aria-label="Portrait of Evan Marsh"></div><div class="name">Evan Marsh</div><div class="cred">PMHNP - BC</div></div>
      <div class="provider"><div class="portrait" role="img" aria-label="Portrait of Lauren Pryce"></div><div class="name">Lauren Pryce</div><div class="cred">PMHNP - BC</div></div>
      <div class="provider"><div class="portrait" role="img" aria-label="Portrait of Neil Corwin"></div><div class="name">Neil Corwin</div><div class="cred">PMHNP - BC</div></div>
      <div class="provider"><div class="portrait" role="img" aria-label="Portrait of Ada Whitcombe"></div><div class="name">Ada Whitcombe</div><div class="cred">PMHNP-BC, DNP</div></div>
    </div>
  </section>

  <div class="brand"><span class="dot"></span><span class="name serif">BRIGHTLOFT CARE</span></div>

  <ul class="contact">
    <li><svg viewBox="0 0 24 24"><path d="M6.6 10.8a15 15 0 006.6 6.6l2.2-2.2a1 1 0 011-.25 11.4 11.4 0 003.6.57 1 1 0 011 1V20a1 1 0 01-1 1A17 17 0 013 4a1 1 0 011-1h3.5a1 1 0 011 1 11.4 11.4 0 00.57 3.6 1 1 0 01-.25 1z" fill="var(--teal)"/></svg>(208)555-7193</li>
    <li><svg viewBox="0 0 24 24"><path d="M12 2a7 7 0 00-7 7c0 5 7 12 7 12s7-7 7-12a7 7 0 00-7-7zm0 9.5A2.5 2.5 0 1112 6.5a2.5 2.5 0 010 5z" fill="var(--teal)"/></svg>412 E Marlowe Coeur d'Alene</li>
    <li><svg viewBox="0 0 24 24"><circle cx="12" cy="12" r="9" fill="none" stroke="var(--teal)" stroke-width="2"/><path d="M3 12h18M12 3c3 3 3 15 0 18M12 3c-3 3-3 15 0 18" fill="none" stroke="var(--teal)" stroke-width="1.6"/></svg>www.BrightLoftCare.com</li>
  </ul>

  <div class="hours"><span class="label">HOURS</span><span class="days">Mon - Thur</span><span class="time">7am - 6pm</span></div>
</main>
</body>
</html>
```